A New and modern Business Card for Tarwick Trade Solutions Ltd

New and modern Logo and Business Card Attached is the current logo/business card designCurrently the business is called "Tarwick & Co." or TTS Ltd for short. This is subject to change.This business specialises in Telecoms and Energy. We work with the major networks (QV, K7, etc) and also offer Energy Products saving clients money off their energy bills.These are business to business services.The current design incorporates a Pheonix, indicating rebirth, starting something new.We would like to maintain the Phoenix element but a newer modern style.We love colours in the logo 3 max.The aim of this is to be ultra slick and modern. I envisage Tarwick & Co. on one side of the card with long descriptions on the other side.Side 1:TTS Ltd/Logo?Side 2:TTS Ltd/Logo/Graphic?Brogan & Co.Name:Address:Phone:Email:The design is mostly flexible but must incorporate a Phoenix.For example "Tarwick & Co." with a block phoenix behind the text...up to you.

Industry/Entity Type

Telecommunications

Contact Information for Business Card

Tarwick & Co.
Address:
Name:
Phone:
Email:

Logo Text

Tarwick & Co.

Colors
33a6d7
0792cd
acd037
9bcb3c
f78f20
fece3e

Requirements
Must have
• Phoenix
• 3/4 colours max
• Blue representing Technology (wireless)
• Green for Eco Energy
• Orange for Phoenix
• White business card background
Should not have
• phoenix must not all be red/ orange fire, we are a technology service company and the phoenix colours must represent this. Fire is not representative of our company.

```html
<!DOCTYPE html>
<html lang="en">
<head>
<meta charset="utf-8">
<title>Tarwick Trade Solutions – Business Card</title>
<link href="https://fonts.googleapis.com/css2?family=Open+Sans:wght@400;600;700&display=swap" rel="stylesheet">
<style>
  :root {
    --backdrop: #4a4a4c;
    --card-dark: #2b2a2b;
    --card-light: #f1f1f0;
    --ink-light: #ffffff;
    --ink-soft: #e4e4e4;
    --ink-grey: #4d4d4f;
    --brand-blue: #33a6d7;
    --icon-ink: #2b2a2b;
  }
  * { box-sizing: border-box; margin: 0; padding: 0; }
  html, body {
    width: 1200px; height: 900px; overflow: hidden;
    background: var(--backdrop);
    font-family: "Open Sans", Arial, sans-serif;
  }
  .canvas {
    position: relative; width: 1200px; height: 900px;
    display: flex; flex-direction: column; align-items: center; justify-content: center; gap: 28px;
  }
  .card {
    position: relative; width: 600px; height: 343px;
    border-radius: 26px; overflow: hidden;
  }
  .card--back { background: var(--card-dark); color: var(--ink-light); }
  .card--front { background: var(--card-light); }

  .brand { display: flex; align-items: center; gap: 10px; }
  .brand__dot { border-radius: 50%; background: var(--brand-blue); flex: none; }
  .brand__name { font-weight: 600; letter-spacing: 0.01em; white-space: nowrap; }

  .card--back .brand { position: absolute; left: 36px; top: 168px; }
  .card--back .brand__dot { width: 26px; height: 26px; }
  .card--back .brand__name { font-size: 12px; color: var(--ink-light); }

  .divider {
    position: absolute; left: 262px; top: 70px; width: 2px; height: 200px;
    background: var(--ink-soft);
  }

  .contact { position: absolute; left: 296px; top: 64px; }
  .contact__name { font-size: 17px; font-weight: 700; letter-spacing: 0.02em; }
  .contact__role { font-size: 12px; color: var(--ink-soft); margin-top: 2px; margin-left: 14px; }
  .contact__list { list-style: none; margin-top: 16px; margin-left: 14px; }
  .contact__item {
    display: flex; align-items: flex-start; gap: 12px;
    font-size: 12px; line-height: 1.3; color: var(--ink-soft); margin-bottom: 11px;
  }
  .contact__icon {
    width: 18px; height: 18px; border-radius: 50%; background: var(--ink-light);
    flex: none; display: flex; align-items: center; justify-content: center;
  }
  .contact__icon svg { width: 11px; height: 11px; }

  .card--front .brand { position: absolute; left: 50%; top: 50%; transform: translate(-50%, -50%); gap: 18px; }
  .card--front .brand__dot { width: 70px; height: 70px; }
  .card--front .brand__name { font-size: 30px; color: var(--ink-grey); }
</style>
</head>
<body>
<main class="canvas">
  <section class="card card--back" aria-label="Business card, contact side">
    <div class="brand">
      <span class="brand__dot" aria-hidden="true"></span>
      <span class="brand__name">Tarwick Trade Solutions</span>
    </div>
    <div class="divider" aria-hidden="true"></div>
    <div class="contact">
      <p class="contact__name">FNAME MNAME LNAME</p>
      <p class="contact__role">Designation</p>
      <ul class="contact__list">
        <li class="contact__item">
          <span class="contact__icon" aria-hidden="true">
            <svg viewBox="0 0 24 24"><path fill="var(--icon-ink)" d="M6.6 10.8a15 15 0 0 0 6.6 6.6l2.2-2.2c.3-.3.7-.4 1-.2 1.1.4 2.300.6 3.6.6.6 0 1 .4 1 1V20c0 .6-.4 1-1 1A17 17 0 0 1 3 4c0-.6.4-1 1-1h3.5c.6 0 1 .4 1 1 0 1.3.2 2.5.6 3.6.1.3 0 .7-.2 1z"/></svg>
          </span>
          <span>123 456 789</span>
        </li>
        <li class="contact__item">
          <span class="contact__icon" aria-hidden="true">
            <svg viewBox="0 0 24 24"><circle cx="12" cy="12" r="4" fill="none" stroke="var(--icon-ink)" stroke-width="2.6"/><path d="M16 8v5.5a2.5 2.5 0 0 0 5 0V12a9 9 0 1 0-3.5 7.1" fill="none" stroke="var(--icon-ink)" stroke-width="2.6"/></svg>
          </span>
          <span>address@email.com</span>
        </li>
        <li class="contact__item">
          <span class="contact__icon" aria-hidden="true">
            <svg viewBox="0 0 24 24"><path fill="var(--icon-ink)" d="M12 2a7 7 0 0 0-7 7c0 5.3 7 13 7 13s7-7.7 7-13a7 7 0 0 0-7-7zm0 9.5A2.5 2.5 0 1 1 12 6.5a2.5 2.5 0 0 1 0 5z"/></svg>
          </span>
          <span>Address Address Address<br>Address Address</span>
        </li>
        <li class="contact__item">
          <span class="contact__icon" aria-hidden="true">
            <svg viewBox="0 0 24 24"><g fill="none" stroke="var(--icon-ink)" stroke-width="2.2"><circle cx="12" cy="12" r="9"/><path d="M3 12h18M12 3c3 3.2 3 14.8 0 18M12 3c-3 3.2-3 14.8 0 18"/></g></svg>
          </span>
          <span>www.webaddress.com</span>
        </li>
      </ul>
    </div>
  </section>

  <section class="card card--front" aria-label="Business card, brand side">
    <div class="brand">
      <span class="brand__dot" aria-hidden="true"></span>
      <span class="brand__name">Tarwick Trade Solutions</span>
    </div>
  </section>
</main>
</body>
</html>
```